Business Cards + Flyer + Letterhead for Care Recruitment Agency

We are a recruitment agency for the health & care sector. We need designs made for business cards, A5 double-sided flyer, and a letterhead template.

Our branding message is professionalism, care, compassion, expertise. We are experts in recruitment for the care & health industry.

Our logo source files and colours are here - https://www.filevault-example.net/sh/q8rn27lpzw4xkc/BBRtLm3QPW92dKfYhNvZceLmo?dl=0

For the business card, I have attached an example we like. We want a vertical business card design, something very similar to the example given. The design should match our logo in terms of brand colors. On one side should be our logo, our website (www.holbrookelune.co.uk) and Care Recruitment Specialists written somewhere visible that fits, between our logo and the website at the bottom. On the other side should be our details.

Details on the front:

Logo with slogan
Care Recruitment Specialists
www.holbrookelune.co.uk

Details on the back:

Dominic Argyros
Managing Director

Radley Court, 40-48 Pellow St, Birmingham, B7 9QX
07612 495137
dominic@holbrookelune.co.uk
www.holbrookelune.co.uk

Nadia Holbrooke
Business Development Director

07731 284956
nadia@holbrookelune.co.uk
www.holbrookelune.co.uk

For the A5 flyer, I have attached some pictures we've used for the website, which could be used for the flyer as well. To get a better idea of our branding, please visit our website - https://holbrookelune.co.uk/

The text for the flyer is also attached.

Finally, the letterhead template should be a docx template with our logo and our identifiable branding (the same shapes and matching colours you will come up with for the business cards and flyer).

```html
<!DOCTYPE html>
<html lang="en">
<head>
<meta charset="utf-8">
<title>Holbrooke Lune – Letterhead</title>
<link href="https://fonts.googleapis.com/css2?family=Montserrat:wght@300;700&family=Roboto+Condensed:wght@300;400&family=Lato:wght@400&display=swap" rel="stylesheet">
<style>
  :root {
    --backdrop: #d6d6d6;
    --paper: #ffffff;
    --text-grey: #5c5c5c;
    --heading-grey: #545454;
    --navy: #1f2d5e;
    --brand-blue: #2f8fd8;
    --signature-tint: #e8ecf5;
  }
  * { margin: 0; padding: 0; box-sizing: border-box; }
  html, body {
    width: 1056px; height: 1200px; overflow: hidden;
    background: var(--backdrop);
  }
  .letterhead {
    position: absolute; left: 104px; top: 0;
    width: 848px; height: 1200px;
    background: var(--paper);
    color: var(--text-grey);
  }
  .brand {
    position: absolute; left: 552px; top: 63px; width: 216px;
    text-align: center;
  }
  .brand-mark {
    display: block; margin: 0 auto 14px;
    width: 86px; height: 86px; border-radius: 50%;
    background: var(--brand-blue);
  }
  .brand-name {
    font-family: "Montserrat", sans-serif; font-weight: 700;
    font-size: 20px; letter-spacing: 2.2px; color: var(--navy);
    line-height: 22px; white-space: nowrap;
  }
  .recipient { position: absolute; left: 80px; top: 278px; }
  .letter-date {
    font-family: "Montserrat", sans-serif; font-weight: 300;
    font-size: 17px; line-height: 22px;
  }
  .recipient-name {
    font-family: "Montserrat", sans-serif; font-weight: 700;
    font-size: 29px; line-height: 36px; color: var(--heading-grey);
    margin-top: 9px; letter-spacing: -0.3px;
  }
  .recipient-title {
    font-family: "Montserrat", sans-serif; font-weight: 300;
    font-size: 17px; line-height: 22px; margin-top: 5px;
  }
  .letter-body {
    position: absolute; left: 80px; top: 430px; width: 688px;
    font-family: "Roboto Condensed", sans-serif; font-weight: 300;
    font-size: 16.5px; line-height: 29.5px; text-align: justify;
  }
  .letter-body p + p { margin-top: 29px; }
  .sign-off {
    position: absolute; left: 80px; top: 880px;
    font-family: "Roboto Condensed", sans-serif; font-weight: 300;
    font-size: 18px; line-height: 24px;
  }
  .signature {
    position: absolute; left: 82px; top: 926px;
    width: 88px; height: 62px; border-radius: 6px;
    background: var(--signature-tint);
  }
  .contact {
    position: absolute; left: 80px; top: 1072px;
    font-family: "Lato", sans-serif; font-size: 16px;
    line-height: 20px; color: var(--navy);
  }
  .contact-address { margin-bottom: 9px; }
  .contact-line { display: flex; align-items: center; height: 21px; }
  .contact-icon { width: 16px; height: 14px; margin-right: 12px; fill: var(--brand-blue); }
  .website {
    position: absolute; right: 80px; top: 1142px;
    font-family: "Lato", sans-serif; font-size: 16.5px;
    line-height: 20px; color: var(--navy);
  }
  .footer-bar {
    position: absolute; left: 576px; bottom: 0;
    width: 192px; height: 15px; background: var(--navy);
  }
</style>
</head>
<body>
  <main class="letterhead">
    <header class="brand">
      <span class="brand-mark" aria-hidden="true"></span>
      <div class="brand-name">HOLBROOKE LUNE</div>
    </header>

    <section class="recipient">
      <p class="letter-date">10 December, 2020</p>
      <h1 class="recipient-name">MARCUS HALE</h1>
      <p class="recipient-title">Cheif Executive Officer</p>
    </section>

    <article class="letter-body">
      <p>Contrary to popular belief, Lorem Ipsum is not simply random text. It has roots in a piece of classical Latin literature from 45 BC, making it over 2000 years old. Howard Pellman, a Latin professor at Ashgrove College in Vermont, looked up one of the more obscure Latin words, consectetur.</p>
      <p>Lorem Ipsum comes from sections 1.10.32 and 1.10.33 of "de Finibus Bonorum et Malorum" (The Extremes of Good and Evil) by Aurelian Tesk, written in 45 BC. This book is a treatise on the theory of ethics, very popular during the Renaissance. The first line of Lorem Ipsum.</p>
      <p>The standard chunk of Lorem Ipsum used since the 1500s is reproduced below for those interested. Sections 1.10.32 and 1.10.33 from "de Finibus Bonorum et Malorum" by Aurelian Tesk are also reproduced in their exact original.</p>
      <p>The standard chunk of Lorem Ipsum used since the 1500s is reproduced below for those interested.</p>
    </article>

    <p class="sign-off">Best Regards</p>
    <div class="signature" role="img" aria-label="Handwritten signature of the sender"></div>

    <footer class="contact">
      <p class="contact-address">Radley Court, 40-48<br>Pellow St, Birmingham, B7 9QX</p>
      <p class="contact-line">
        <svg class="contact-icon" viewBox="0 0 16 16" aria-hidden="true"><path d="M3.6 1.2l2.3 2.6c.4.4.4 1 0 1.4L4.8 6.4c.9 2 2.6 3.8 4.7 4.8l1.2-1.2c.4-.4 1-.4 1.4 0l2.6 2.3c.4.4.4 1 0 1.4l-1.4 1.4c-.6.6-1.5.8-2.3.5C6.3 14 2 9.7.4 5.1.1 4.3.3 3.4.9 2.8l1.3-1.6c.4-.4 1-.4 1.4 0z"/></svg>
        07612 495137
      </p>
      <p class="contact-line">
        <svg class="contact-icon" viewBox="0 0 16 12" aria-hidden="true"><path d="M0 0h16v12H0z" opacity=".9"/><path d="M0 0l8 6.5L16 0" fill="none" stroke="#fff" stroke-width="1.3"/></svg>
        dominic@holbrookelune.co.uk
      </p>
    </footer>

    <p class="website">www.holbrookelune.co.uk</p>
    <div class="footer-bar" aria-hidden="true"></div>
  </main>
</body>
</html>
```